CODED website - Breakfree418

I am a successful entrepreneur - have recently sold my business and am semi-retired. I want to give something back, as well as provide a blog for articles and my journeys.

I will also be using this to provide free business and entrepreneurial advice.

I am creating a NOT FOR PROFIT business called Breakfree418.com.au which will provide the following;

1. Blog and articles; my travels, Small to Medium business advice and articles

2. My Bucket List - the 100 things I aim to achieve

3. Free business / start up advice - a section on the website which provides case studies on people / businesses which ask me for advice. We will then chronicle their story and what advice we have given for them to succeed.

My inspiration is the Martin Oxendale idea and website;

http://martinoxendale.example/about-martin/

Obviously I do NOT want a copy of this site, but use this for inspiration.

Furthermore, I would be interested in ongoing collaboration with the successful designer - I will be providing advice and consultancy to start ups, all of which will need web design etc, so there is ongoing referral streams for the successful designer.

I need this to be CODED and then uplifted to the website, so please DO NOT bid on this unless you can provide a coded site and facilitate the upload to BrightHosting.

The NECESSARY tabs / pages

Main landing page - a short introduction into the ethos of Breakfree418

Writing - this will be the blog articles

About

Our Bucket List - a section where we can add our 100 buket list items. Hyperlinked to open a new page which has details on each bucket list item (ie #1 Make Breakfree418 - hyperlink to a new page which then has info on the bucklist item and what we have done)

Breakfree418 - this will be the section where we discuss people / businesses that we are helping. We will have an opening intro section + a link to the contact us page so they can ask us for the free advice. This will be the section where we have case studies into businesses / people that we have helped.

Hey everyone!

I'm really keen to get this website launched and looking amazing - if you have any questions, or would like to discuss anything at all, please email me at

dane@pollwick.example.com.au

As I mentioned in the brief, I am doing this site to give back; I will not be earning a cent, and I will not be trying to earn any funds. I'm doing it simply to help other start ups or entrepreneurs, so I really want this site to look amazing.

I hope someone reads this and is inspired, and wants to be involved in this social enterprise with me.

Really excited to hear from you all and see your designs!

Industry/Entity Type

Business

Requirements
Must have
• MUST BE CODED and uplifted to the BrightHosting registered domain - www.breakfree418.com.au - happy to discuss additional costings for this with successful designer.

Separate pages for each section (as outlined in the brief above)

Blog section to look similar to http://martinoxendale.example/3x5/

Comprehensive website - not a simple wordpress template theme with some minor modifications. I will immediately reject any simple template design. I am looking for a slick, fully functioning website design.

PLEASE BE AWARE that I am looking for ongoing collaboration with the www.breakfree418.com.au.

I am trying this website as I want to find a young, energetic, vibrant, dynamic designer - this is your opportunity to be a part of something big, as this website will be huge!

Please do not submit a design if you are not motivated and ready for something big.

```html
<!DOCTYPE html>
<html lang="en">
<head>
<meta charset="utf-8">
<title>Breakfree418</title>
<link href="https://fonts.googleapis.com/css2?family=Ubuntu:wght@300;400;500&display=swap" rel="stylesheet">
<style>
:root{
  --bg:#5a2a21;
  --bg-dark:#4c2219;
  --cream:#fef5e4;
  --cream-2:#fdf3e1;
  --sand:#f5e2bd;
  --gold:#d5ae46;
  --gold-light:#e1c06a;
  --brown:#6b2b1b;
  --rust:#9c3d17;
  --text:#7c6a5c;
  --muted:#b79b83;
  --badge:#f0d9ae;
  --foot:#b8927f;
}
*{margin:0;padding:0;box-sizing:border-box}
html,body{width:1059px;height:1200px;overflow:hidden;background:var(--bg)}
body{font-family:'Ubuntu',sans-serif}
.stage{position:absolute;left:0;top:0;width:1280px;height:1450px;transform:scale(0.82734);transform-origin:0 0;background:var(--bg)}
.abs{position:absolute}
.skyline{left:120px;top:0;width:1110px;height:200px;background:linear-gradient(180deg,rgba(70,28,20,0) 0%,rgba(70,28,20,.55) 45%,rgba(70,28,20,.35) 100%)}

.header{left:160px;top:146px;width:960px;height:115px;background:var(--cream);box-shadow:0 4px 10px rgba(0,0,0,.25)}
.logo{left:29px;top:38px;font-size:36px;font-weight:400;letter-spacing:2px;color:var(--brown)}
.nav{right:40px;top:44px;display:flex;gap:0;list-style:none}
.nav li{font-size:14px;color:var(--brown);padding:6px 0;margin-left:37px;position:relative}
.nav li.active{background:var(--rust);color:#fff;padding:6px 15px;border-radius:4px}
.nav li.active::after{content:"";position:absolute;left:50%;bottom:-6px;margin-left:-5px;border:5px solid transparent;border-top-color:var(--rust);border-bottom:0}

.band{left:160px;top:282px;width:960px;height:111px;background:linear-gradient(180deg,var(--gold) 0%,var(--gold-light) 100%)}
.feature{left:160px;top:393px;width:960px;height:279px;background:var(--cream-2)}
.hero-frame{left:183px;top:320px;width:611px;height:347px;background:#fcf3e2}
.hero-img{left:192px;top:329px;width:593px;height:329px;background:linear-gradient(180deg,#c9a16a 0%,#e8d2a6 28%,#9aa6b2 55%,#6f7c88 78%,#b3a081 100%)}
.pager{left:215px;top:349px;display:flex;gap:2px}
.pager span{width:17px;height:18px;background:#4a4038;color:#fff;font-size:12px;text-align:center;line-height:18px}
.pager span.on{background:var(--gold)}
.hero-caption{left:213px;top:577px;font-size:26px;color:rgba(255,255,255,.6)}

.services-title{left:815px;top:346px;font-size:24px;color:var(--brown)}
.ticks{list-style:none}
.ticks li{position:relative;padding-left:17px;font-size:12.5px;line-height:24px;color:var(--text)}
.ticks li::before{content:"";position:absolute;left:0;top:8px;border:3.5px solid transparent;border-left:4px solid #a89080;border-right:0}
.services{left:815px;top:416px;width:270px}
.services li{margin-bottom:24px}

.lower{left:160px;top:672px;width:960px;height:680px;background:linear-gradient(180deg,#f7e6c4 0%,var(--sand) 100%)}
.latest{left:189px;top:698px;width:605px;height:302px;background:var(--cream-2);border:4px solid #fdf7ec}
.h2{font-size:18px;color:var(--brown);font-weight:400}
.latest .h2{position:absolute;left:16px;top:18px}
.thumb{background:linear-gradient(180deg,#8fa2bd 0%,#c7c6c4 55%,#6e6658 100%)}
.thumb.warm{background:linear-gradient(135deg,#c47b2e 0%,#e8b066 50%,#8a5a2a 100%)}
.art-title{font-size:14px;color:var(--brown)}
.art-text{font-size:11.5px;line-height:18px;color:var(--text);text-align:justify}
.badge{height:21px;background:var(--badge);border-radius:2px;color:#fff;font-size:12px;display:flex;align-items:center;gap:5px;padding:0 7px}
.badge svg{display:block}

.recent{left:814px;top:698px;width:287px;height:302px;background:var(--cream-2)}
.recent-head{height:42px;background:var(--gold);color:var(--brown);font-size:16px;padding:11px 21px}
.recent .ticks{position:absolute;left:21px;top:66px}
.recent li{margin-bottom:12px}

.advice-box{left:193px;top:1072px;width:272px;height:250px;background:var(--cream-2)}
.adv-thumb{width:94px;height:64px}
.adv-text{font-size:12.5px;line-height:20px;color:var(--brown);width:140px}
.video{left:487px;top:1072px;width:305px;height:175px;background:linear-gradient(180deg,#e4e2de 0%,#b9b7b2 45%,#7d7d76 70%,#6f8f4e 85%,#55554f 100%)}
.video-bar{left:487px;top:1225px;width:305px;height:22px;background:#22201e}
.ethos-text{left:487px;top:1275px;width:310px;font-size:11px;line-height:18px;color:var(--text)}
.bucket{left:814px;top:1070px;list-style:none}
.bucket li{position:relative;padding-left:19px;font-size:12.5px;color:#a8643e;margin-bottom:21px}
.bucket li::before{content:"";position:absolute;left:0;top:5px;width:6px;height:6px;border:1px solid #d6b592;border-radius:50%}

.footer{top:1393px;font-size:12px;color:var(--foot)}
.social-dot{width:22px;height:22px;border-radius:50%;background:#8d6a5c;top:1390px}
</style>
</head>
<body>
<div class="stage">
  <div class="abs skyline" role="img" aria-label="Faint city skyline silhouette behind the header"></div>

  <header class="abs header">
    <div class="abs logo">BREAKFREE418</div>
    <ul class="abs nav">
      <li class="active">ABOUT</li>
      <li>PLACES</li>
      <li>BUSINESS ADIVSE</li>
      <li>CONTACT</li>
    </ul>
  </header>

  <div class="abs band"></div>
  <div class="abs feature"></div>
  <div class="abs hero-frame"></div>
  <div class="abs hero-img" role="img" aria-label="Traveller photographing mountains from a rocky outcrop under a golden sky"></div>
  <div class="abs pager"><span>1</span><span>2</span><span>3</span><span class="on">4</span></div>
  <div class="abs hero-caption">My bucket list....</div>

  <h2 class="abs services-title" style="font-weight:400">Our Services</h2>
  <ul class="abs ticks services">
    <li>Nunc in ipsum quam, vitae congue odio.</li>
    <li>Quisque a est est, vitae posuere purus.</li>
    <li>Pellentesque et felis ut justo vulputate sollicitudin quis et est.</li>
    <li>Nunc id quam eu orci aliquet faucibus sed eu neque.</li>
  </ul>

  <div class="abs lower"></div>

  <section class="abs latest">
    <h2 class="h2">Latest Travel Articles</h2>
    <div class="abs thumb" style="left:16px;top:64px;width:140px;height:82px" role="img" aria-label="Business travellers standing on an open plain"></div>
    <div class="abs art-title" style="left:172px;top:64px">World wide business tour</div>
    <div class="abs badge" style="left:498px;top:56px"><svg width="14" height="11" viewBox="0 0 14 11"><path d="M1 1h12v7H6l-3 3V8H1z" fill="#fff"/></svg>3</div>
    <div class="abs badge" style="left:541px;top:56px"><svg width="12" height="12" viewBox="0 0 12 12"><path d="M6 0l1.8 3.8 4.2.5-3.1 2.9.8 4.1L6 9.3 2.3 11.3l.8-4.1L0 4.3l4.2-.5z" fill="#fff"/></svg>8</div>
    <p class="abs art-text" style="left:172px;top:91px;width:405px">Sed ut perspiciatis unde omnis iste natus error sit voluptatem accusantium doloremque laudantium, totam rem aperiam, eaque ipsa qitae dicta sunt explicabo.</p>

    <div class="abs thumb warm" style="left:16px;top:194px;width:140px;height:82px" role="img" aria-label="Friends laughing together at a holiday celebration"></div>
    <div class="abs art-title" style="left:172px;top:194px">Holiday tour around the world</div>
    <div class="abs badge" style="left:495px;top:186px"><svg width="14" height="11" viewBox="0 0 14 11"><path d="M1 1h12v7H6l-3 3V8H1z" fill="#fff"/></svg>3</div>
    <div class="abs badge" style="left:538px;top:186px"><svg width="12" height="12" viewBox="0 0 12 12"><path d="M6 0l1.8 3.8 4.2.5-3.1 2.9.8 4.1L6 9.3 2.3 11.3l.8-4.1L0 4.3l4.2-.5z" fill="#fff"/></svg>8</div>
    <p class="abs art-text" style="left:174px;top:220px;width:400px">Sed ut perspiciatis unde omnis iste natus error sit voluptatem accusantium doloremque laudantium, totam rem aperiam, eaquet quasi architecto beatae vitae dicta sunt explicabo.</p>
  </section>

  <aside class="abs recent">
    <div class="recent-head">Recent Articles</div>
    <ul class="ticks">
      <li>2012 Annual Review: Travel Roundup</li>
      <li>2012 Annual Review: Overview</li>
      <li>A Challenging Question</li>
      <li>Getting to Guinea Bissau</li>
      <li>Famous Last Words</li>
      <li>Top 10 Articles</li>
    </ul>
  </aside>

  <h2 class="abs h2" style="left:212px;top:1026px">Business Advice</h2>
  <div class="abs advice-box"></div>
  <div class="abs adv-thumb thumb" style="left:210px;top:1086px;background:linear-gradient(135deg,#2a2f4a,#7a5a4a)" role="img" aria-label="Entrepreneur in conversation"></div>
  <div class="abs adv-text" style="left:317px;top:1082px">Entrepreneurs Need to Know Before Starting a Business</div>
  <div class="abs adv-thumb thumb" style="left:210px;top:1166px;background:linear-gradient(180deg,#f39a4e,#e98a3c)" role="img" aria-label="Laptop on an orange desk"></div>
  <div class="abs adv-text" style="left:317px;top:1161px">3 Ways to Recruit Talent for a Hungry Startup</div>
  <div class="abs adv-thumb thumb" style="left:210px;top:1248px;background:linear-gradient(180deg,#e0c28a,#b98a3a 60%,#8a6a2a)" role="img" aria-label="Person resting in a golden field"></div>
  <div class="abs adv-text" style="left:317px;top:1243px">6 Essential Time Savers for Overworked Young Entrepreneurs</div>

  <h2 class="abs h2" style="left:487px;top:1026px">Ethos of Breakfree418</h2>
  <div class="abs video" role="img" aria-label="Video still of a race car speeding past a stadium"></div>
  <svg class="abs" style="left:626px;top:1135px" width="20" height="34" viewBox="0 0 20 34"><path d="M0 0l20 17L0 34z" fill="#1e1c1a"/></svg>
  <div class="abs video-bar">
    <svg width="305" height="22" viewBox="0 0 305 22">
      <g fill="#fff">
        <rect x="9" y="7" width="1.6" height="8"/><path d="M17 7v8l-6-4z"/>
        <rect x="35" y="7" width="2.2" height="8"/><rect x="39.5" y="7" width="2.2" height="8"/>
        <path d="M61 7v8l6-4z"/><rect x="67" y="7" width="1.6" height="8"/>
        <path d="M288 6h3v1h-2v2h-1zM296 6h-3v1h2v2h1zM288 16h3v-1h-2v-2h-1zM296 16h-3v-1h2v-2h1z"/>
      </g>
    </svg>
  </div>
  <p class="abs ethos-text">Sed ut perspiciatis unde omnis iste natus error sit volupta-tem accusantium doloremque laudantium.</p>

  <h2 class="abs h2" style="left:814px;top:1026px">My Bucket list</h2>
  <ul class="abs bucket">
    <li>Write a hit country song</li>
    <li>Run with the bulls in Pamplona</li>
    <li>Throw tomatoes at La Tomatina</li>
    <li>Climb Kilimanjaro</li>
    <li>Walk the Camino de Santiago</li>
  </ul>

  <footer>
    <div class="abs footer" style="left:162px">Copyright © 2012. All Rights Reserved</div>
    <div class="abs footer" style="left:531px">Terms &amp; Condition &nbsp;&nbsp;|&nbsp;&nbsp; Privacy Policy</div>
    <div class="abs footer" style="left:944px">Social Media</div>
    <div class="abs social-dot" style="left:1036px"></div>
    <div class="abs social-dot" style="left:1065px"></div>
    <div class="abs social-dot" style="left:1096px"></div>
  </footer>
</div>
</body>
</html>
```